Hemp company needs website/online store

We are a startup hemp company and we need an online storefront designed. We are very open do design, but will include our logo to help. We make 100% hemp derived products like edibles, concentrates, vapes and THCA flower. Everything is grown locally, and all products are extracted and made in house.

• I would like to highlight that we have Cannabis products that are hemp derived and 100% legal across the US. Also that all cannabis is locally grown and products are extracted and made in house and sent out for third party lab testing.

```html
<!DOCTYPE html>
<html lang="en">
<head>
<meta charset="utf-8">
<title>Sunny Leaf Hemp</title>
<link href="https://fonts.googleapis.com/css2?family=Poppins:wght@400;500;600;700&display=swap" rel="stylesheet">
<style>
:root{
  --lime:#9cb93a;
  --btn:#8bb33a;
  --green:#5d8f2f;
  --deep:#4f8a3c;
  --ink:#2b2b2b;
  --muted:#555;
  --soft:#f0f0f0;
  --footer:#2d2d2d;
  --white:#fff;
}
*{box-sizing:border-box;margin:0;padding:0}
html,body{width:1200px;height:4862px;overflow:hidden}
body{font-family:'Poppins',sans-serif;color:var(--ink);background:var(--white);position:relative}
section,header,footer,.topbar{position:absolute;left:0;width:1200px}
.abs{position:absolute}
.center{text-align:center;left:0;width:1200px}
.btn{position:absolute;background:var(--btn);color:var(--white);border-radius:30px;display:flex;align-items:center;justify-content:center;font-weight:600;gap:10px}
h2.sec{position:absolute;left:0;width:1200px;text-align:center;font-size:37px;font-weight:500;color:var(--ink)}

.topbar{top:0;height:60px;background:var(--lime);color:var(--white);font-size:16px;font-weight:500;display:flex;align-items:center;justify-content:center}

header{top:60px;height:165px}
.brand{left:70px;top:24px;width:230px}
.brand-mark{width:56px;height:56px;border:3px solid var(--green);border-radius:50%;margin:0 auto 8px}
.brand-name{font-size:28px;font-weight:600;color:var(--green);text-align:center;line-height:1.1;white-space:nowrap}
.phone{left:650px;top:48px;font-size:19px;font-weight:500;color:var(--green);display:flex;align-items:center;gap:6px}
.search{left:855px;top:32px;width:271px;height:57px;border:1px solid #d9d9d9;border-radius:30px;font-size:14px;color:#777;display:flex;align-items:center;padding:0 18px;justify-content:space-between}
.nav{left:398px;top:118px;display:flex;gap:40px;font-size:16px;font-weight:500;align-items:center}
.nav .on{color:var(--green)}

.hero{top:225px;height:624px;background:radial-gradient(ellipse at 30% 40%,#a4641c,#5a3210 55%,#2a1a0c)}
.hero h1{top:155px;font-size:58px;line-height:58px;font-weight:700;color:var(--white)}
.hero p{top:290px;font-size:28px;line-height:40px;font-weight:600;color:var(--white)}
.hero .btn{left:506px;top:400px;width:188px;height:51px;font-size:20px}

.cats{top:849px;height:515px}
.cats h2.sec{top:55px}
.cat{position:absolute;top:140px;width:242px}
.cat .ph{height:241px;border-radius:10px}
.cat span{display:block;text-align:center;margin-top:18px;font-size:18px;font-weight:600;color:var(--green)}

.promo{top:1364px;height:544px;background:linear-gradient(180deg,#3d3d3d,#4a4a46 60%,#3b4130)}
.promo p{top:130px;font-size:34px;line-height:45px;font-weight:600;color:var(--white)}
.promo .btn{left:487px;top:353px;width:226px;height:51px;font-size:22px;font-weight:500}

.featured{top:1908px;height:634px}
.featured h2.sec{top:55px}
.prod{position:absolute;top:136px;width:242px}
.prod .ph{height:260px;border-radius:10px}
.prod h3{margin-top:22px;font-size:19px;font-weight:500;color:var(--green)}
.prod p{font-size:15px;line-height:26px;color:var(--ink);margin-top:4px}
.prod .row{display:flex;align-items:center;gap:18px;margin-top:18px;font-size:15px;font-weight:600}
.prod .row b{background:var(--btn);color:var(--white);border-radius:20px;width:117px;height:40px;display:flex;align-items:center;justify-content:center;font-size:14px;font-weight:500}
.arrow{position:absolute;width:24px;height:24px}

.news{top:2542px;height:268px;background:linear-gradient(90deg,#3f6e22,#6e9e3a 50%,#3f6e22)}
.news h2{top:50px;font-size:38px;font-weight:500;color:var(--white)}
.news p{top:108px;font-size:15px;color:var(--white)}
.news .field{left:287px;top:160px;width:630px;height:53px;background:var(--white);border-radius:30px;overflow:hidden;display:flex}
.news .field span{flex:1;padding-left:24px;display:flex;align-items:center;font-size:14px}
.news .field b{width:158px;background:var(--btn);color:var(--white);font-size:16px;font-weight:600;display:flex;align-items:center;justify-content:center;gap:10px}

.testi{top:2810px;height:543px}
.testi h2.sec{top:55px}
.tcard{position:absolute;top:134px;width:508px;height:281px;background:#efefef;border-radius:16px;text-align:center}
.stars{margin-top:26px;color:#86b43c;font-size:22px;letter-spacing:6px}
.tcard p{font-size:17px;line-height:30px;color:#333;margin:8px 20px 0;white-space:nowrap}
.tcard h4{margin-top:8px;font-size:20px;font-weight:600;color:var(--green)}
.avatar{position:absolute;left:201px;top:228px;width:106px;height:106px;border-radius:50%;background:radial-gradient(circle,#8a7056,#3b3027);border:3px solid var(--white)}

.blog{top:3353px;height:685px;background:#efefef}
.blog h2.sec{top:62px}
.post{position:absolute;top:161px;width:328px;text-align:center}
.post .ph{height:230px;border-radius:10px}
.post h3{margin-top:22px;font-size:24px;line-height:30px;font-weight:600;color:var(--green);white-space:nowrap}
.post p{margin-top:12px;font-size:15px;line-height:28px;color:#333;white-space:nowrap;margin-left:-10px;margin-right:-10px}
.post a{display:block;margin-top:14px;font-size:15px;font-weight:500;color:var(--green);text-decoration:none}

.perks{top:4038px;height:213px}
.perk{position:absolute;top:59px;width:328px;height:154px;background:var(--deep);color:var(--white);text-align:center;padding-top:22px}
.perk h3{margin-top:10px;font-size:24px;font-weight:500}
.perk p{font-size:15px;margin-top:4px}

footer{top:4251px;height:611px;background:var(--footer);color:var(--white)}
.flogo{left:70px;top:125px;width:230px}
.flogo .brand-mark{border-color:#7cae3a}
.flogo .brand-name{color:#8cbf3c}
.ftext{left:75px;top:300px;width:240px;font-size:15px;line-height:29px}
.fcol{top:118px}
.fcol h4{font-size:23px;font-weight:600;margin-bottom:12px}
.fcol li{list-style:none;font-size:15px;line-height:38px}
.social{display:flex;gap:16px;margin-top:4px}
.social i{width:26px;height:26px;border-radius:50%;background:var(--white)}
.bottom{left:0;top:523px;width:1200px;height:88px;border-top:1px solid #444;display:flex;align-items:center;justify-content:space-between;padding:0 74px 0 75px;font-size:14px}
.cards{display:flex;gap:8px}
.cards i{width:41px;height:25px;background:#e6e6e6;border-radius:3px}
</style>
</head>
<body>

<div class="topbar">Neque porro quisquam est, qui dolorem</div>

<header>
  <div class="abs brand"><div class="brand-mark"></div><div class="brand-name">Sunny Leaf Hemp</div></div>
  <div class="abs phone">
    <svg width="18" height="18" viewBox="0 0 24 24"><path d="M6.6 10.8c1.4 2.8 3.8 5.1 6.6 6.6l2.2-2.2c.3-.3.7-.4 1-.2 1.1.4 2.3.6 3.6.6.6 0 1 .4 1 1V20c0 .6-.4 1-1 1C10.6 21 3 13.4 3 4c0-.6.4-1 1-1h3.5c.6 0 1 .4 1 1 0 1.3.2 2.5.6 3.6.1.3 0 .7-.2 1z" fill="#5d8f2f"/></svg>
    +1 555-014-2290
  </div>
  <div class="abs search">Search
    <svg width="18" height="18" viewBox="0 0 24 24"><circle cx="10" cy="10" r="6.5" fill="none" stroke="#5d8f2f" stroke-width="3"/><path d="M15 15l6 6" stroke="#5d8f2f" stroke-width="3"/></svg>
  </div>
  <nav class="abs nav">
    <span class="on">Home</span><span>About Us</span><span>Categories</span><span>Products</span><span>Blog</span><span>Contact</span>
    <svg width="20" height="20" viewBox="0 0 24 24"><circle cx="12" cy="7" r="5" fill="#2b2b2b"/><path d="M2 23c0-6 4-9 10-9s10 3 10 9z" fill="#2b2b2b"/></svg>
    <svg width="22" height="20" viewBox="0 0 24 22"><path d="M1 8h22l-3 13H4z M7 8l5-7 5 7" fill="#2b2b2b" stroke="#2b2b2b" stroke-width="2"/></svg>
  </nav>
</header>

<section class="hero" role="img" aria-label="Amber hemp oil in a glass beside green cannabis leaves">
  <h1 class="abs center">Welcome to<br>Sunny Leaf Hemp</h1>
  <p class="abs center">Sed ut perspiciatis unde omnis iste natus<br>error sit voluptatem.</p>
  <div class="btn">Shop Now</div>
</section>

<section class="cats">
  <h2 class="sec">Categories</h2>
  <div class="cat" style="left:75px"><div class="ph" role="img" aria-label="Blue edible cubes with a hemp leaf" style="background:linear-gradient(160deg,#4f7e2c,#6e9dc2)"></div><span>Edibles</span></div>
  <div class="cat" style="left:345px"><div class="ph" role="img" aria-label="Golden concentrate dripping from a tool" style="background:radial-gradient(circle at 50% 60%,#d69218,#3a2408 70%)"></div><span>Concentrates</span></div>
  <div class="cat" style="left:615px"><div class="ph" role="img" aria-label="Vape cartridge among hemp plants" style="background:linear-gradient(180deg,#5c8a3a,#c9d8b0)"></div><span>Vapes</span></div>
  <div class="cat" style="left:885px"><div class="ph" role="img" aria-label="Hand holding a THCA flower bud" style="background:linear-gradient(160deg,#9aa08a,#5f6b3e 60%,#c89a84)"></div><span>THCA Flowers</span></div>
</section>

<section class="promo" role="img" aria-label="Dropper bottles of hemp oil among leaves on a dark background">
  <p class="abs center">We have Cannabis products that are hemp derived and<br>100% legal across the US. all cannabis is locally grown and<br>products are extracted and made in house and sent<br>out for third party lab testing.</p>
  <div class="btn">Shop Now
    <svg width="20" height="16" viewBox="0 0 20 16"><path d="M1 8h16M11 2l6 6-6 6" fill="none" stroke="#fff" stroke-width="2.6"/></svg>
  </div>
</section>

<section class="featured">
  <h2 class="sec">Featured</h2>
  <svg class="arrow" style="left:39px;top:316px" viewBox="0 0 24 24"><path d="M16 2L6 12l10 10" fill="none" stroke="#333" stroke-width="2.4"/></svg>
  <svg class="arrow" style="left:1135px;top:316px" viewBox="0 0 24 24"><path d="M8 2l10 10L8 22" fill="none" stroke="#333" stroke-width="2.4"/></svg>
  <div class="prod" style="left:75px"><div class="ph" role="img" aria-label="Amber concentrate product photo" style="background:radial-gradient(circle at 50% 55%,#f3d38a,#efefef 60%)"></div><h3>Name Heading</h3><p>Neque porro quisquam est<br>commodo</p><div class="row">$170<b>Buy Now</b></div></div>
  <div class="prod" style="left:343px"><div class="ph" role="img" aria-label="Vape pen product photo" style="background:radial-gradient(circle at 50% 60%,#d4d4d0,#efefef 60%)"></div><h3>Name Heading</h3><p>Neque porro quisquam est<br>commodo</p><div class="row">$170<b>Buy Now</b></div></div>
  <div class="prod" style="left:615px"><div class="ph" role="img" aria-label="Gummies with hemp leaves product photo" style="background:radial-gradient(circle at 50% 55%,#e6d9a0,#efefef 60%)"></div><h3>Name Heading</h3><p>Neque porro quisquam est<br>commodo</p><div class="row">$170<b>Buy Now</b></div></div>
  <div class="prod" style="left:885px"><div class="ph" role="img" aria-label="Dried hemp flower bud product photo" style="background:radial-gradient(circle at 50% 50%,#c3c4b0,#efefef 60%)"></div><h3>Name Heading</h3><p>Neque porro quisquam est<br>commodo</p><div class="row">$170<b>Buy Now</b></div></div>
</section>

<section class="news" role="img" aria-label="Blurred green hemp leaves background">
  <h2 class="abs center">Subscribe to Our Newsletter</h2>
  <p class="abs center">Neque porro quisquam est commodo &nbsp;enim ipsam voluptatem quia voluptas sit aspernatur aut odit aut fugita</p>
  <div class="abs field"><span>Enter Email Address</span><b>Subscribe
    <svg width="14" height="12" viewBox="0 0 20 16"><path d="M1 8h16M11 2l6 6-6 6" fill="none" stroke="#fff" stroke-width="3"/></svg></b></div>
</section>

<section class="testi">
  <h2 class="sec">Customer Testimonials</h2>
  <svg class="arrow" style="left:39px;top:261px" viewBox="0 0 24 24"><path d="M16 2L6 12l10 10" fill="none" stroke="#333" stroke-width="2.4"/></svg>
  <svg class="arrow" style="left:1135px;top:261px" viewBox="0 0 24 24"><path d="M8 2l10 10L8 22" fill="none" stroke="#333" stroke-width="2.4"/></svg>
  <div class="tcard" style="left:83px"><div class="stars">★★★★★</div><p>“ Sed ut perspiciatis unde omnis iste natus<br>error sit voluptatem accusantium doloremque<br>laudantium, totam rem aperiam, eaque ipsa<br>quae ab illo inventore veritatis..”</p><h4>Name Heading</h4><div class="avatar" role="img" aria-label="Customer portrait"></div></div>
  <div class="tcard" style="left:619px"><div class="stars">★★★★★</div><p>“ Sed ut perspiciatis unde omnis iste natus<br>error sit voluptatem accusantium doloremque<br>laudantium, totam rem aperiam, eaque ipsa<br>quae ab illo inventore veritatis..”</p><h4>Name Heading</h4><div class="avatar" role="img" aria-label="Customer portrait"></div></div>
</section>

<section class="blog">
  <h2 class="sec">Latest Blog Articles</h2>
  <div class="post" style="left:74px"><div class="ph" role="img" aria-label="Woman examining a hemp bud" style="background:linear-gradient(135deg,#6b4a30,#a8b56a)"></div><h3>Sed ut perspiciatis unde<br>omnis iste natus.</h3><p>Neque porro quisquam est commodo<br>enim ipsam voluptatem quia voluptas sit<br>aspernatur aut odit aut fugita</p><a>Read More →</a></div>
  <div class="post" style="left:436px"><div class="ph" role="img" aria-label="Oil bottles and hemp buds on a wooden table" style="background:linear-gradient(180deg,#eeeeea,#d6c49a 60%,#8a5a36)"></div><h3>Sed ut perspiciatis unde<br>omnis iste natus.</h3><p>Neque porro quisquam est commodo<br>enim ipsam voluptatem quia voluptas sit<br>aspernatur aut odit aut fugita</p><a>Read More →</a></div>
  <div class="post" style="left:798px"><div class="ph" role="img" aria-label="Gloved hand tending hemp plants" style="background:linear-gradient(135deg,#3f6a26,#8fb35c 60%,#dfe6d0)"></div><h3>Sed ut perspiciatis unde<br>omnis iste natus.</h3><p>Neque porro quisquam est commodo<br>enim ipsam voluptatem quia voluptas sit<br>aspernatur aut odit aut fugita</p><a>Read More →</a></div>
</section>

<section class="perks">
  <div class="perk" style="left:74px">
    <svg width="48" height="40" viewBox="0 0 48 40"><ellipse cx="20" cy="15" rx="18" ry="12" fill="#fff"/><ellipse cx="30" cy="24" rx="16" ry="11" fill="#fff" stroke="#4f8a3c" stroke-width="3"/></svg>
    <h3>Sunt Explicabo</h3><p>Neque porro quisquam est commodo</p></div>
  <div class="perk" style="left:436px">
    <svg width="44" height="40" viewBox="0 0 44 40"><path d="M16 4L3 16l13 12v-8c12 0 20 4 24 14 0-14-8-24-24-24z" fill="#fff"/></svg>
    <h3>Sunt Explicabo</h3><p>Neque porro quisquam est commodo</p></div>
  <div class="perk" style="left:798px">
    <svg width="52" height="40" viewBox="0 0 52 40"><rect x="14" y="2" width="36" height="28" rx="3" fill="#fff"/><path d="M14 12H6l-5 8v10h13z" fill="#fff"/><circle cx="12" cy="33" r="5" fill="#fff" stroke="#4f8a3c" stroke-width="2"/><circle cx="38" cy="33" r="5" fill="#fff" stroke="#4f8a3c" stroke-width="2"/></svg>
    <h3>Sunt Explicabo</h3><p>Neque porro quisquam est commodo</p></div>
</section>

<footer>
  <div class="abs flogo"><div class="brand-mark"></div><div class="brand-name">Sunny Leaf Hemp</div></div>
  <p class="abs ftext">Sed ut perspiciatis unde omnis iste natus error sit voluptatem accusantium do loremque laudantium, totam rem aperiam.</p>
  <div class="abs fcol" style="left:360px"><h4>Quick Links</h4><ul><li>Home</li><li>About Us</li><li>Categories</li><li>Products</li><li>Blog</li><li>Contact</li></ul></div>
  <div class="abs fcol" style="left:615px"><h4>Support</h4><ul><li>Sed ut perspiciatis</li><li>Unde omnis iste natus</li><li>Error sit &nbsp;voluptatem</li><li>Accusantium do</li><li>loremque laudantium</li><li>Totam rem</li></ul></div>
  <div class="abs fcol" style="left:885px"><h4>Follow Us</h4><div class="social"><i></i><i></i><i></i><i></i><i></i></div></div>
  <div class="abs bottom"><span>© Copyright 2023 Companya Name All Right Reserved</span>
    <div class="cards"><i></i><i></i><i></i><i></i><i></i><i></i><i></i><i></i><i></i><i></i><i></i></div></div>
</footer>

</body>
</html>
```